Business Card Design Project

We have recently completed CraftHive projects for a new logo and wesbite.
We now require new business cards.
We hand out very little printed material to clients as all information is online. When we do hand out something, like a business card, we want it to have real impact and make a statement about the quality and professionalism of our company.
We have an idea of what we want our card to look like but we want a designer to make sure they have impact and look great.
Our requirements are…
Size: 85mm X 55mm - Landscape
Front of card: Logo plus the following contact information.
Dennis Marlow
Operations Manager
Phone +44(0) 1632 xxx xxx
Mobile +44(0) 7700 xxx xxx
Email denmo@korvantix.example
Address 17 Pellick Row, Aberdeen AB12 9QZ
Website www.korvantix.example
How you layout the front of the card is up to you, we would like to see some different ideas. Attached are two versions of our logo that may be used.
Back of card: We would like this to be simple but again have impact. Our current thought is to have the logo or just the large W design from the logo in white against a dark background, perhaps made up from the dark green in the logo.
The logos are attached so you can see the colours in them but the dark ones are..
Dark Blue = C:88, M:55, Y:44, K:28
Dark Green = C:87, M:53, Y:50, K:50
We sometimes also use a bright orange as an accent or highlight colour…
Orange: = C:0, M:39, Y:94, K:0

```html
<!DOCTYPE html>
<html lang="en">
<head>
<meta charset="utf-8">
<title>Korvantix Systems – Business Cards</title>
<link href="https://fonts.googleapis.com/css2?family=Source+Sans+3:wght@400;600;700&display=swap" rel="stylesheet">
<style>
  :root {
    --ink-dark: #22434b;
    --ink-teal: #5a8f99;
    --ink-olive: #7d915c;
    --paper: #ffffff;
    --stage: #ebe8e3;
    --text-body: #2c3a3e;
    --card-radius: 14px;
    --card-shadow: 0 4px 12px rgba(0,0,0,0.18);
  }
  * { box-sizing: border-box; margin: 0; padding: 0; }
  html, body {
    width: 1200px; height: 800px; overflow: hidden;
    background: var(--stage);
    font-family: "Source Sans 3", "Myriad Pro", sans-serif;
  }
  .canvas { position: relative; width: 1200px; height: 800px; }

  .card {
    position: absolute; width: 500px; height: 324px;
    border-radius: var(--card-radius);
    box-shadow: var(--card-shadow);
    overflow: hidden;
  }
  .card--front { left: 82px; top: 62px; background: var(--paper); }
  .card--back-dark { left: 610px; top: 68px; background: var(--ink-dark); }
  .card--back-gradient { left: 86px; top: 408px;
    background: linear-gradient(90deg, var(--ink-dark) 0%, #4f6a55 50%, var(--ink-olive) 100%); }
  .card--back-light { left: 612px; top: 408px; background: var(--paper); }

  /* front */
  .front-band { position: absolute; left: 0; top: 0; width: 500px; height: 324px; }
  .brand-block {
    position: absolute; left: 40px; top: 130px;
    display: flex; align-items: center; gap: 10px;
  }
  .brand-dot { width: 18px; height: 18px; border-radius: 50%; background: var(--ink-dark); }
  .brand-name {
    font-weight: 700; font-size: 34px; letter-spacing: 1px;
    color: var(--ink-dark); line-height: 1;
  }
  .contact { position: absolute; left: 286px; top: 66px; color: var(--text-body); }
  .contact__name { font-weight: 700; font-size: 19px; color: var(--ink-dark); letter-spacing: 0.3px; }
  .contact__role { font-size: 14px; margin-top: 1px; }
  .contact__list { list-style: none; margin-top: 14px; font-size: 14px; line-height: 19px; }
  .contact__list li { display: flex; align-items: center; gap: 5px; }
  .contact__list svg { width: 10px; height: 10px; flex: none; }
  .address {
    position: absolute; left: 291px; top: 273px;
    color: var(--paper); font-size: 14px; line-height: 19px;
  }

  /* backs */
  .back-mark {
    position: absolute; left: 0; right: 0; top: 118px;
    display: flex; justify-content: center; align-items: center; gap: 14px;
  }
  .back-mark__name { font-weight: 700; font-size: 56px; letter-spacing: 2px; line-height: 1; }
  .back-mark__dot { width: 26px; height: 26px; border-radius: 50%; }
  .back-url {
    position: absolute; left: 0; right: 0; top: 266px; text-align: center;
    font-size: 16px; letter-spacing: 2.6px;
  }
  .on-dark .back-mark__name, .on-dark .back-url { color: var(--paper); }
  .on-dark .back-mark__dot { background: var(--paper); }
  .on-light .back-mark__name { color: var(--ink-dark); }
  .on-light .back-mark__dot { background: var(--ink-teal); }
  .on-light .back-url { color: var(--ink-dark); }
</style>
</head>
<body>
<main class="canvas">

  <section class="card card--front" aria-label="Business card front">
    <svg class="front-band" viewBox="0 0 500 324" aria-hidden="true">
      <path d="M0,232 C120,262 220,270 300,256 C380,242 440,220 500,214 L500,324 L0,324 Z" fill="var(--ink-dark)"/>
      <path d="M0,224 C120,254 220,262 300,248 C380,234 440,212 500,206" fill="none" stroke="var(--ink-teal)" stroke-width="2"/>
    </svg>

    <div class="brand-block">
      <span class="brand-dot"></span>
      <span class="brand-name">KORVANTIX</span>
    </div>

    <div class="contact">
      <p class="contact__name">DENNIS MARLOW</p>
      <p class="contact__role">Operations Manager</p>
      <ul class="contact__list">
        <li><svg viewBox="0 0 10 10"><circle cx="5" cy="5" r="4.4" fill="none" stroke="var(--ink-dark)" stroke-width="1"/><path d="M3.2,2.6 L4.2,2.6 L4.6,4 L4,4.5 C4.4,5.4 4.8,5.8 5.6,6.1 L6.1,5.5 L7.4,5.9 L7.4,6.9 C5,7 3,5 3.2,2.6 Z" fill="var(--ink-dark)"/></svg>+44(0) 1632 xxx xxx</li>
        <li><svg viewBox="0 0 10 10"><rect x="2.6" y="0.6" width="4.8" height="8.8" rx="0.8" fill="var(--ink-dark)"/><rect x="3.4" y="1.6" width="3.2" height="5" fill="var(--paper)"/></svg>+44(0) 7700 xxx xxx</li>
        <li><svg viewBox="0 0 10 10"><rect x="0.6" y="2.2" width="8.8" height="6" fill="var(--ink-dark)"/><path d="M0.8,2.4 L5,5.8 L9.2,2.4" fill="none" stroke="var(--paper)" stroke-width="0.8"/></svg>denmo@korvantix.example</li>
        <li><svg viewBox="0 0 10 10"><circle cx="5" cy="5" r="4.3" fill="none" stroke="var(--ink-dark)" stroke-width="1"/><ellipse cx="5" cy="5" rx="1.8" ry="4.3" fill="none" stroke="var(--ink-dark)" stroke-width="0.8"/><path d="M0.8,5 H9.2" stroke="var(--ink-dark)" stroke-width="0.8"/></svg>www.korvantix.example</li>
      </ul>
    </div>

    <p class="address">17 Pellick Row,<br>Aberdeen AB12 9QZ</p>
  </section>

  <section class="card card--back-dark on-dark" aria-label="Business card back, dark">
    <div class="back-mark"><span class="back-mark__dot"></span><span class="back-mark__name">KORVANTIX</span></div>
    <p class="back-url">www.korvantix.example</p>
  </section>

  <section class="card card--back-gradient on-dark" aria-label="Business card back, gradient">
    <div class="back-mark"><span class="back-mark__dot"></span><span class="back-mark__name">KORVANTIX</span></div>
    <p class="back-url">www.korvantix.example</p>
  </section>

  <section class="card card--back-light on-light" aria-label="Business card back, light">
    <div class="back-mark"><span class="back-mark__dot"></span><span class="back-mark__name">KORVANTIX</span></div>
    <p class="back-url">www.korvantix.example</p>
  </section>

</main>
</body>
</html>
```